Business Card & Email Signature Design || Upmarket + Luxury

Rima Vale Honey, a New Zealand Manuka Honey company needs a Business Card & Email Signature design.

Our logo's are attached in Gold & Black versions, feel free to be creative with how you use the logo and it's patterns in your design.

Style:
- Looking for an Elegant, Luxurious, Upmarket feel.
- Black/Matte Black Card, Gold Foil, UV Embossing

Information to Add:

- Logo
- Company Name: Rima Vale Honey
- Name: Martin Holloway
- Title: Creative Director
- Phone: +64 2815 96 417
- Email: martin@rimavalehoney.example.nz
- Website: www.rimavalehoney.example.nz

- Socials: ***For email Signature Only***
- Facebook: https://www.facebook.com/rimavalehoney/
- Instagram: https://www.instagram.com/rimavalehoney/

Target Market(s)

Asia/Europe Luxury, Upmarket

Contact Information for Business Card

- Logo
- Name: Martin Holloway
- Phone: +64 2815 96 417

Font styles to use
Other font styles liked:
• Champagne & Limousines (Attached)

Requirements
Must have
• Business Card & Email Signature Design.

Looking for a Sleek, Luxury, Upmarket Design.

```html
<!DOCTYPE html>
<html lang="en">
<head>
<meta charset="utf-8">
<title>Rima Vale Honey — Business Card</title>
<link rel="stylesheet" href="https://fonts.googleapis.com/css2?family=Montserrat:wght@400;500;700&display=swap">
<style>
  :root {
    --stage: #1c1c1c;
    --card: #111111;
    --card-edge: #1a1a1a;
    --gold: #d9b867;
    --gold-soft: #b8954f;
    --ink-light: #e8e4dc;
    --faint: rgba(255, 255, 255, 0.035);
  }
  * { box-sizing: border-box; margin: 0; padding: 0; }
  html, body {
    width: 1200px; height: 780px; overflow: hidden;
    background: var(--stage);
    font-family: "Montserrat", Arial, sans-serif;
  }
  .stage {
    width: 1200px; height: 780px;
    display: flex; align-items: center; justify-content: center; gap: 40px;
  }
  .card {
    position: relative;
    width: 540px; height: 310px;
    background: var(--card);
    border-radius: 26px;
    box-shadow: 0 18px 40px rgba(0,0,0,0.55), inset 0 0 0 1px var(--card-edge);
    overflow: hidden;
  }
  /* Front */
  .pattern-field {
    position: absolute; left: 110px; top: 20px;
    width: 320px; height: 270px; border-radius: 50%;
    background: radial-gradient(closest-side, var(--faint), transparent);
  }
  .front-brand {
    position: absolute; inset: 0;
    display: flex; align-items: center; justify-content: center; gap: 14px;
  }
  .brand-dot {
    width: 14px; height: 14px; border-radius: 50%;
    background: var(--gold);
  }
  .brand-name {
    color: var(--gold);
    font-weight: 500;
    letter-spacing: 0.22em;
    text-transform: uppercase;
    white-space: nowrap;
  }
  .front-brand .brand-name { font-size: 26px; }
  /* Back */
  .back-brand {
    position: absolute; right: 40px; top: 70px;
    display: flex; align-items: center; gap: 10px;
  }
  .back-brand .brand-name { font-size: 21px; }
  .gold-rule {
    position: absolute; left: 250px; right: 40px; top: 150px;
    height: 1px; background: var(--gold-soft);
  }
  .holder {
    position: absolute; left: 40px; top: 132px;
  }
  .holder-name {
    color: var(--gold); font-weight: 700; font-size: 20px;
    letter-spacing: 0.04em; text-transform: uppercase;
  }
  .holder-title {
    color: var(--ink-light); font-size: 13px; margin-top: 3px;
  }
  .contacts {
    position: absolute; left: 40px; top: 196px;
    list-style: none;
  }
  .contacts li {
    display: flex; align-items: center; gap: 12px;
    color: var(--ink-light); font-size: 12.5px; letter-spacing: 0.04em;
    height: 24px;
  }
  .contacts svg { width: 13px; height: 13px; fill: var(--gold); flex: none; }
  .footer-brand {
    position: absolute; right: 40px; bottom: 40px;
  }
  .footer-brand .brand-name { font-size: 12px; letter-spacing: 0.2em; }
</style>
</head>
<body>
<main class="stage">
  <section class="card card--front" aria-label="Card front">
    <div class="pattern-field" role="img" aria-label="Faint embossed koru bee pattern"></div>
    <div class="front-brand">
      <span class="brand-dot"></span>
      <span class="brand-name">Rima Vale Honey</span>
    </div>
  </section>

  <section class="card card--back" aria-label="Card back">
    <div class="back-brand">
      <span class="brand-dot"></span>
      <span class="brand-name">Rima Vale Honey</span>
    </div>
    <div class="gold-rule"></div>
    <div class="holder">
      <p class="holder-name">Martin Holloway</p>
      <p class="holder-title">Creative Director</p>
    </div>
    <ul class="contacts">
      <li>
        <svg viewBox="0 0 24 24" aria-hidden="true"><path d="M6.6 10.8a15 15 0 0 0 6.6 6.6l2.2-2.2c.3-.3.7-.4 1-.2 1.1.4 2.3.6 3.6.6.6 0 1 .4 1 1V20c0 .6-.4 1-1 1A17 17 0 0 1 3 4c0-.6.4-1 1-1h3.5c.6 0 1 .4 1 1 0 1.3.2 2.5.6 3.6.1.3 0 .7-.2 1z"/></svg>
        +64 2815 96 417
      </li>
      <li>
        <svg viewBox="0 0 24 24" aria-hidden="true"><path d="M2 5h20v14H2zm2 2v.5l8 5 8-5V7zm0 3v7h16v-7l-8 5z"/></svg>
        martin@rimavalehoney.example.nz
      </li>
      <li>
        <svg viewBox="0 0 24 24" aria-hidden="true"><path d="M12 2a10 10 0 1 0 0 20 10 10 0 0 0 0-20zm-1 17.9A8 8 0 0 1 4.1 11H7c.1 3.2 1.6 6.4 4 8.9zM7 9H4.1A8 8 0 0 1 11 4.1C8.6 6.6 7.1 9 7 9zm6 10.9c2.4-2.5 3.9-5.7 4-8.9h2.9a8 8 0 0 1-6.9 8.9zM17 9c-.1-2.2-1.6-4.4-4-4.9A8 8 0 0 1 19.9 9zM9 11h6c-.1 2.6-1.2 5.2-3 7.2-1.8-2-2.9-4.6-3-7.2zm0-2c.1-2 1.2-4 3-5.6 1.8 1.6 2.9 3.6 3 5.6z"/></svg>
        www.rimavalehoney.example.nz
      </li>
    </ul>
    <div class="footer-brand">
      <span class="brand-name">Rima Vale Honey</span>
    </div>
  </section>
</main>
</body>
</html>
```